Judicial election website to attract voters

I need a simple one-page web design for a judicial election. I'm going to put up one picture, maybe two. The picture I have needs a little touch-up (whiten teeth for example). I have 3 paragraphs of text. I'd like a "Donate" button that can link to a CoinDrift account. I'd also like a little background design, like the Constitution or something like that. There's a couple other little things but that's the bulk of it.

Target Market(s)

Involved voters and some media

Industry/Entity Type

Legal

Number of Pages Required

1 page

Font styles to use
Sans Serif

Requirements
Must have
• My picture, text, donate button
• Phrase "Remember to vote August 30, 2016!"
Nice to have
• Perhaps a second photo, maybe a short 30 second video of me talking directly to the voters, cool background: Constitution, something judgey.
Should not have
• Not sure ... profanity, I guess.

```html
<!DOCTYPE html>
<html lang="en">
<head>
<meta charset="utf-8">
<title>Delaney for Judge</title>
<link rel="stylesheet" href="https://fonts.googleapis.com/css2?family=Raleway:wght@400;500;600;700&family=Roboto:wght@400;500&display=swap">
<style>
:root{
  --orange:#e8492b;
  --ink:#111214;
  --text:#555;
  --light:#efefef;
  --white:#fff;
  --button-dark:#2b2b2d;
}
*{box-sizing:border-box;margin:0;padding:0}
html,body{width:1200px;height:2273px;overflow:hidden}
body{position:relative;font-family:"Raleway",sans-serif;background:var(--white);color:var(--text)}
a{text-decoration:none}
.abs{position:absolute}

/* header + hero */
.hero{left:0;top:0;width:1200px;height:586px;background:linear-gradient(180deg,#4a5fd4 0%,#6b7bd6 35%,#8a8f9a 60%,#4b5a3a 85%,#2d3a22 100%)}
.navbar{left:0;top:27px;width:1200px;height:81px;background:rgba(255,255,255,.88)}
.brand{left:0;top:27px;width:371px;height:81px;background:var(--orange);clip-path:polygon(0 0,100% 0,85% 100%,0 100%);display:flex;align-items:center;padding-left:100px;gap:14px}
.brand-mark{width:22px;height:22px;border:3px solid var(--white)}
.brand-name{font-weight:700;font-size:22px;color:var(--white);letter-spacing:.5px}
.nav{left:560px;top:27px;height:81px;display:flex;align-items:center}
.nav a{font-weight:500;font-size:16px;color:#222;margin-right:55px}
.nav a:last-child{margin-right:0}
.callout{left:604px;top:224px;width:497px;height:265px;background:rgba(0,0,0,.72);padding:38px 36px 0;text-align:right}
.callout-text{font-family:"Roboto",sans-serif;font-size:33px;line-height:58px;color:var(--white)}
.btn-vote{display:inline-block;margin-top:20px;width:145px;height:50px;line-height:50px;text-align:center;background:var(--orange);color:var(--white);font-family:"Roboto",sans-serif;font-weight:500;font-size:19px;border-radius:3px}

/* features */
.feature{top:594px;width:389px;height:232px;color:var(--white);text-align:center;overflow:hidden}
.feature-bg{left:0;top:0;width:100%;height:100%}
.feature-body{position:relative;padding-top:36px}
.feature-icon{display:block;margin:0 auto;height:50px}
.feature-title{font-weight:600;font-size:21px;margin-top:18px;letter-spacing:.3px}
.feature-text{font-size:13px;line-height:22px;margin:12px auto 0;width:330px}

/* about */
.portrait-frame{left:98px;top:874px;width:369px;height:461px;border:2px solid #ddd;padding:6px}
.portrait{width:100%;height:100%;background:linear-gradient(180deg,#d8d8d6 0%,#c9b59a 40%,#d98a63 80%,#e08a66 100%)}
.about{left:504px;top:868px;width:597px}
.about-title{font-weight:500;font-size:33px;color:var(--orange);display:inline-block;padding-bottom:6px;border-bottom:2px solid var(--orange)}
.about-text{font-size:12px;line-height:24px;color:var(--text);margin-top:12px}
.about-text + .about-text{margin-top:6px}

/* vote band */
.vote-band{left:0;top:1394px;width:1200px;height:342px;background:linear-gradient(90deg,#6c7386 0%,#5a6586 40%,#3a4490 70%,#2e3a8a 100%)}
.vote-art{left:125px;top:1420px;width:360px;height:316px;background:linear-gradient(180deg,#e65a2e 0%,#9fd23c 35%,#5bb4e8 55%,#d9b089 80%,#c99a76 100%);opacity:.85}
.video{left:659px;top:1430px;width:427px;height:265px;border:3px solid var(--white);background:linear-gradient(180deg,#8a8f96 0%,#5d5650 50%,#3a3330 100%)}
.video-bar{left:12px;bottom:10px;right:12px;height:22px;background:rgba(0,0,0,.55);border-radius:2px}
.video-progress{left:12px;top:9px;width:270px;height:4px;background:#999}
.video-progress i{display:block;width:135px;height:4px;background:#1e9ad6}

/* partners */
.partners{left:0;top:1736px;width:1200px;height:188px;background:var(--light)}
.arrow{top:1819px;width:40px;height:40px;border:1.5px solid #222;border-radius:50%;background:var(--white);display:flex;align-items:center;justify-content:center}
.partner-row{left:120px;top:1828px;width:965px;display:flex;justify-content:space-between;align-items:center}
.partner{display:flex;align-items:center;gap:8px;font-weight:600;font-size:16px;color:#555}
.partner i{width:16px;height:16px;background:#666;display:block}

/* cta */
.cta{left:0;top:1924px;width:1200px;height:91px;background:var(--orange)}
.cta-text{left:98px;top:1943px;width:545px;font-weight:600;font-size:17px;line-height:28px;color:var(--white)}
.btn-donate{left:914px;top:1942px;width:172px;height:53px;border-radius:27px;background:var(--button-dark);color:var(--white);font-weight:600;font-size:15px;text-align:center;line-height:53px}

/* footer */
.footer{left:0;top:2015px;width:1200px;height:258px;background:linear-gradient(180deg,#1b1e24 0%,#101216 100%)}
.social{top:2057px;left:443px;display:flex;gap:23px}
.social span{width:45px;height:45px;border:2px solid var(--white);border-radius:50%;display:flex;align-items:center;justify-content:center;color:var(--white);font-weight:700;font-size:17px}
.footer-nav{left:0;top:2138px;width:1200px;display:flex;justify-content:center;font-weight:500;font-size:14px;color:var(--white)}
.footer-nav a{color:var(--white)}
.footer-nav b{font-weight:400;margin:0 33px}
.footer-rule{left:98px;top:2191px;width:1003px;height:1px;background:#3a3d44}
.copyright{left:0;top:2222px;width:1200px;text-align:center;font-size:14px;color:var(--white)}
</style>
</head>
<body>

<div class="abs hero" role="img" aria-label="State capitol building with columns and dome at dusk, framed by trees"></div>
<div class="abs navbar"></div>
<div class="abs brand"><span class="brand-mark"></span><span class="brand-name">DELANEY</span></div>
<nav class="abs nav">
  <a href="#">HOME</a><a href="#">ABOUT</a><a href="#">EVENT</a><a href="#">PRESS RELEASE</a><a href="#">CONTACT</a>
</nav>
<div class="abs callout">
  <p class="callout-text">" REMEMBER TO VOTE<br>AUGUST 30, 2016! "</p>
  <span class="btn-vote">VOTE ME</span>
</div>

<section class="abs feature" style="left:8px">
  <div class="abs feature-bg" role="img" aria-label="Campaign volunteers with orange overlay" style="background:linear-gradient(135deg,#f05a36,#e0432a)"></div>
  <div class="feature-body">
    <svg class="feature-icon" viewBox="0 0 50 50" width="50" height="50"><rect x="6" y="26" width="38" height="20" fill="#fff"/><rect x="14" y="24" width="22" height="4" fill="#e8492b"/><rect x="18" y="6" width="14" height="20" fill="#fff" transform="rotate(-12 25 16)"/></svg>
    <h3 class="feature-title">EXPERIENCED</h3>
    <p class="feature-text">Nemo enim ipsam voluptatem quia voluptas sit asper natur aut odit aut fugit, sed quia consequuntur magni dolores eos qui ratione voluptatem</p>
  </div>
</section>
<section class="abs feature" style="left:406px">
  <div class="abs feature-bg" role="img" aria-label="Flag-waving crowd under dark overlay" style="background:linear-gradient(135deg,#23262c,#0d0e11)"></div>
  <div class="feature-body">
    <svg class="feature-icon" viewBox="0 0 60 50" width="60" height="50"><path d="M6 22 L30 12 L54 22 Z" fill="#fff"/><rect x="28.5" y="2" width="1.5" height="10" fill="#fff"/><path d="M30 2 h8 v5 h-8z" fill="#fff"/><rect x="6" y="24" width="48" height="3" fill="#fff"/><g fill="#fff"><rect x="9" y="29" width="4" height="12"/><rect x="17" y="29" width="4" height="12"/><rect x="25" y="29" width="4" height="12"/><rect x="33" y="29" width="4" height="12"/><rect x="41" y="29" width="4" height="12"/><rect x="49" y="29" width="3" height="12"/></g><rect x="4" y="43" width="52" height="4" fill="#fff"/></svg>
    <h3 class="feature-title">DEDICATED</h3>
    <p class="feature-text">Nemo enim ipsam voluptatem quia voluptas sit asper natur aut odit aut fugit, sed quia consequuntur magni dolores eos qui ratione voluptatem</p>
  </div>
</section>
<section class="abs feature" style="left:803px">
  <div class="abs feature-bg" role="img" aria-label="Audience at a rally under dark overlay" style="background:linear-gradient(135deg,#1e2024,#0b0c0e)"></div>
  <div class="feature-body">
    <svg class="feature-icon" viewBox="0 0 50 50" width="50" height="50"><rect x="10" y="10" width="30" height="34" fill="none" stroke="#fff" stroke-width="4"/></svg>
    <h3 class="feature-title">RESPECTED</h3>
    <p class="feature-text">Nemo enim ipsam voluptatem quia voluptas sit asper natur aut odit aut fugit, sed quia consequuntur magni dolores eos qui ratione voluptatem</p>
  </div>
</section>

<div class="abs portrait-frame"><div class="portrait" role="img" aria-label="Portrait photo of the candidate, coral top"></div></div>
<section class="abs about">
  <h2 class="about-title">About Me</h2>
  <p class="about-text">Delaney was born and raised in Tampa Florida, the daughter of an air-conditioning repairman who later opened his own successful business. As the first in her family to go to college, her parents could not have been more proud as she finished her degree at Gulfshore State University, then continued on to Coastal State College of Law where she graduated with honors.</p>
  <p class="about-text">Dedicating her life to public service in central Florida, she has spent the last 18 years as a prosecutor fighting for victims of child abuse and sexual abuse in Orange and Osceola counties. She participates in local charities such as the Full Table Food Pantry and the Open Page Reading Circle. Delaney shares her knowledge and experience freely, often mentoring the other young prosecutors and lecturing on jury selection and trial strategies. She is also committed to ensuring ethical behavior in the profession of law. In law school, she won an award for ethics and professionalism but since then she also served as Chair of a Bar Grievance Committee, which handles complaints and ethical violations committed by local attorneys.</p>
  <p class="about-text">The cornerstone of Delaney's candidacy for judge is her experience in the courtroom. Nobody knows how to run an efficient courtroom better than an attorney who has litigated a hundred felony jury trials and argued more pretrial motions than can be counted. But even a judge with all the right knowledge and experience cannot excel without the correct temperament.</p>
</section>

<div class="abs vote-band" role="img" aria-label="State flag and capitol with blue overlay"></div>
<div class="abs vote-art" role="img" aria-label="Hands holding up colourful letters spelling vote"></div>
<div class="abs video" role="img" aria-label="Video player showing a crowd at a rally">
  <div class="abs video-bar"><div class="abs video-progress"><i></i></div></div>
</div>

<div class="abs partners"></div>
<div class="abs arrow" style="left:32px"><svg width="12" height="14" viewBox="0 0 12 14"><path d="M8 2 L3 7 L8 12" fill="none" stroke="#222" stroke-width="2"/></svg></div>
<div class="abs arrow" style="left:1128px"><svg width="12" height="14" viewBox="0 0 12 14"><path d="M4 2 L9 7 L4 12" fill="none" stroke="#222" stroke-width="2"/></svg></div>
<div class="abs partner-row">
  <span class="partner"><i></i>KROVANT</span>
  <span class="partner"><i></i>BRIXOMEL</span>
  <span class="partner"><i></i>TARNWELL HAUL</span>
  <span class="partner"><i></i>Plovique</span>
  <span class="partner"><i></i>ROUTANEX</span>
  <span class="partner"><i></i>WELVORA</span>
</div>

<div class="abs cta"></div>
<p class="abs cta-text">The cornerstone of Delaney's candidacy for judge is her experience in the courtroom.</p>
<a class="abs btn-donate" href="#" aria-label="Donate via CoinDrift">DONATE</a>

<footer>
  <div class="abs footer" role="img" aria-label="Dark city skyline at night"></div>
  <div class="abs social">
    <span aria-label="Friendly">F</span>
    <span aria-label="Chirper">C</span>
    <span aria-label="Searchly">S</span>
    <span aria-label="Feed"><svg width="18" height="18" viewBox="0 0 18 18"><circle cx="3" cy="15" r="2.2" fill="#fff"/><path d="M1.5 8 A8.5 8.5 0 0 1 10 16.5" fill="none" stroke="#fff" stroke-width="2"/><path d="M1.5 2 A14.5 14.5 0 0 1 16 16.5" fill="none" stroke="#fff" stroke-width="2"/></svg></span>
    <span aria-label="Snapframe">P</span>
  </div>
  <nav class="abs footer-nav">
    <a href="#">HOME</a><b>|</b><a href="#">ABOUT</a><b>|</b><a href="#">EVENTS</a><b>|</b><a href="#">CONTACT</a><b>|</b><a href="#">PRESS RELEASE</a>
  </nav>
  <div class="abs footer-rule"></div>
  <p class="abs copyright">© 2016 Delaney. All Rights Reserved</p>
</footer>

</body>
</html>
```